Advertising Portal Needs eBrochure

Hi Crowders! Our advertising portal, which focus on the new launches property, needs an online brochure to promote to potential advertisers the benefits of advertising their projects with us. These advertisers will be mainly real estate developers and agencies.

WHAT WE LOOKING FOR
We do not want over-fanciful designs that makes the content hard to read. The use of illustrations and graphics/symbols related to covered topics are encouraged. The overall design should portrait our advertising efficiency through online and social media means. Our website - www.brightkeyhomes.sg.

For draft purposes, just do up the front page, back page, and few inner pages, preferably to include one illustration chart (either on page 7/8). Size wise probably A5 portrait or landscape, for future printing into a booklet.

WORK COMPLETION AND PAYMENT
The $500 stated here is 50% of the payment. Upon getting a desired draft design, we will need you to work on the full content with slight amendments along the way. Once done, we will be paying the balance $500, and we will need the pdf file as well as the work file.

Let your design juice flow, and hope we can work with you!
Updates

Hi Crowders! Thank you for your submissions. We are closing the project as we've decided on a design. It's a pity we can only select one design, as there are a number of good works. Hope we will have a chance to work together on our upcoming projects. Cheers =)

Target Market(s)

Real estate developers, real estate agencies, and perhaps to an extent, individual property sales agent.

Industry/Entity Type

Advertising

Requirements
Should not have
• We prefer not to have much real people kind of stock images. Try not to use images from our portal as we do not have the ownerships. Instead, you can use stock images of property developments artist impression that gives a similar feel.

```html
<!DOCTYPE html>
<html lang="en">
<head>
<meta charset="utf-8">
<title>Email Blasting – Active Marketing</title>
<link rel="stylesheet" href="https://fonts.googleapis.com/css2?family=PT+Serif:ital,wght@0,400;0,700;1,400&display=swap">
<style>
  :root {
    --canvas: #ffffff;
    --page: #e7e8e7;
    --ink: #1e1e1e;
    --ink-soft: #555a55;
    --green: #3c9a3a;
    --green-line: #4aa54a;
    --frame: #a9cf86;
    --callout: #dfe9b6;
    --tab: #8f9190;
    --search: #3aa88f;
    --social: #a6cb3a;
    --press: #1d97d4;
  }
  * { margin: 0; padding: 0; box-sizing: border-box; }
  html, body { width: 1200px; height: 846px; overflow: hidden; background: var(--canvas); }
  body { position: relative; font-family: "PT Serif", Georgia, serif; color: var(--ink); }
  .page {
    position: absolute; left: 87px; top: 22px; width: 1104px; height: 801px;
    background: var(--page);
  }
  .section-title {
    position: absolute; left: 116px; top: 55px;
    font-size: 17px; font-weight: 700; letter-spacing: 1.6px;
  }
  .intro {
    position: absolute; top: 86px;
    font-size: 17px; line-height: 27px; white-space: nowrap;
  }
  .intro--left { left: 116px; }
  .intro--right { left: 641px; }
  .diagram { position: absolute; left: 0; top: 0; }
  .callout-text { font-size: 17px; font-weight: 700; letter-spacing: 1.6px; fill: var(--ink-soft); }
  .stat-figure { font-size: 20px; letter-spacing: 2px; fill: var(--green); }
  .stat-label { font-size: 11.5px; letter-spacing: 1.6px; fill: var(--ink-soft); }
  .channel-name { font-size: 13px; font-weight: 700; fill: #ffffff; }
  .project-label { font-size: 13px; font-weight: 700; fill: var(--ink); }
  .caption { font-size: 12px; font-style: italic; fill: var(--ink-soft); }
  .page-number { font-size: 15px; font-weight: 700; fill: var(--ink); }
</style>
</head>
<body>
  <div class="page"></div>

  <h2 class="section-title">EMAIL BLASTING</h2>
  <p class="intro intro--left">Want immediate attention for a new launch project?<br>A promotion? A Re-launch? Or project coming to completion?<br>Consumers are always interested with such events. Let us help<br>you to spread this to public by notifying our subscribers, as well<br>as local agents, on such important updates through our emails<br>blasting service.</p>
  <p class="intro intro--right">How is it different from sending your own? Well, beside avoiding<br>the hassle - a trusted name, recognized server, and a well-<br>designed newsletter - will better catch the recipients attention,<br>less likely to end in spam, and our targeted recipients are<br>consumers with genuine interest and our subscribers numbers<br>are growing fast.</p>

  <svg class="diagram" width="1200" height="846" viewBox="0 0 1200 846">
    <defs>
      <linearGradient id="project-tones" x1="0" y1="0" x2="1" y2="1">
        <stop offset="0" stop-color="#2f9a3e"/>
        <stop offset="0.55" stop-color="#9fcc3c"/>
        <stop offset="1" stop-color="#c9cccb"/>
      </linearGradient>
      <marker id="arrowhead" viewBox="0 0 10 10" refX="9" refY="5" markerWidth="8" markerHeight="8" orient="auto">
        <path d="M0 1 L10 5 L0 9 Z" fill="var(--green-line)"/>
      </marker>
    </defs>

    <!-- callout -->
    <rect x="398" y="292" width="405" height="91" fill="#ffffff"/>
    <rect x="404" y="298" width="393" height="79" fill="var(--callout)"/>
    <path d="M580 383 L616 383 L598 408 Z" fill="#ffffff"/>
    <text class="callout-text" x="605" y="330" text-anchor="middle">HOW OUR MARKETING CAMPAIGNS</text>
    <text class="callout-text" x="605" y="354" text-anchor="middle">BOOST YOUR PROJECT AWARENESS</text>

    <!-- channels -->
    <rect x="200" y="458" width="110" height="60" fill="var(--search)"/>
    <circle cx="217" cy="488" r="7" fill="#ffffff" opacity="0.85"/>
    <text class="channel-name" x="230" y="492">Searchly</text>
    <rect x="200" y="520" width="110" height="60" fill="var(--social)"/>
    <circle cx="217" cy="550" r="7" fill="#ffffff" opacity="0.85"/>
    <text class="channel-name" x="230" y="554">Friendbook</text>
    <rect x="200" y="582" width="110" height="60" fill="var(--press)"/>
    <circle cx="217" cy="612" r="7" fill="#ffffff" opacity="0.85"/>
    <text class="channel-name" x="230" y="608">Harbour</text>
    <text class="channel-name" x="230" y="624">Daily</text>

    <!-- connectors in -->
    <g stroke="var(--green-line)" stroke-width="1.5" fill="none">
      <path d="M322 490 L427 522"/>
      <path d="M322 568 L427 604"/>
      <path d="M322 640 L427 685"/>
    </g>
    <g fill="var(--green-line)">
      <circle cx="427" cy="522" r="4"/>
      <circle cx="427" cy="604" r="4"/>
      <circle cx="427" cy="685" r="4"/>
      <circle cx="781" cy="522" r="4"/>
      <circle cx="781" cy="604" r="4"/>
      <circle cx="781" cy="685" r="4"/>
    </g>

    <!-- stats -->
    <g fill="#ffffff" stroke="var(--frame)" stroke-width="1.5">
      <rect x="427" y="493" width="354" height="58"/>
      <rect x="427" y="573" width="354" height="64"/>
      <rect x="427" y="653" width="354" height="63"/>
    </g>
    <text class="stat-figure" x="604" y="525" text-anchor="middle">TENS OF THOUSANDS</text>
    <text class="stat-label" x="604" y="542" text-anchor="middle">OF GENUINE PROPERTY SEARCHERS MONTHLY</text>
    <text class="stat-figure" x="604" y="602" text-anchor="middle">60,000 TO 100,000</text>
    <text class="stat-label" x="604" y="620" text-anchor="middle">TARGETED CONSUMERS PER CAMPAIGN</text>
    <text class="stat-figure" x="604" y="684" text-anchor="middle">HUNDREDS OF THOUSANDS</text>
    <text class="stat-label" x="604" y="701" text-anchor="middle">OF EYEBALLS</text>

    <!-- project artwork -->
    <rect x="852" y="362" width="296" height="290" rx="6" fill="url(#project-tones)" role="img" aria-label="Illustration of green high-rise towers with trees on a grey plot"/>

    <!-- connectors out -->
    <g stroke="var(--green-line)" stroke-width="1.5" fill="none" marker-end="url(#arrowhead)">
      <path d="M781 522 L890 488"/>
      <path d="M781 604 L890 570"/>
      <path d="M781 685 L890 655"/>
    </g>

    <text class="project-label" x="905" y="672" transform="rotate(14 905 672)">Your Project</text>

    <text class="caption" x="595" y="779" text-anchor="middle">Illustration 1: Active Marketing</text>

    <!-- page tab -->
    <path d="M1178 766 L1191 772 L1191 808 L1178 808 L1166 790 Z" fill="var(--tab)"/>
    <text class="page-number" x="1172" y="796">7</text>
  </svg>
</body>
</html>
```